Harborlight Amusement Collective (HAC)

We need a business card design for Harborlight Amusement Collective. Modern and sleek looking, with all critical information. Open to single or double sided designs, if double sided info needs to be all on one side. The main Logo is Harborlight Amusement collective and must be on the card. The other three logos are for the brands that fall under the group, they might be good on the back.

Industry/Entity Type

Business

```html
<!DOCTYPE html>
<html lang="en">
<head>
<meta charset="utf-8">
<title>Harborlight Amusement Collective – Business Card</title>
<link rel="stylesheet" href="https://fonts.googleapis.com/css2?family=Montserrat:wght@500;600;700;800&family=Roboto+Condensed:wght@700&display=swap">
<style>
  :root {
    --blue: #2457a0;
    --green: #8aa83c;
    --ink: #2a2a2a;
    --paper: #ffffff;
    --backdrop: #d9d9d9;
    --divider: #8a8a8a;
  }
  html, body { margin: 0; padding: 0; overflow: hidden; }
  p { margin: 0; }
  body {
    width: 1200px; height: 852px;
    background: var(--backdrop);
    position: relative;
    font-family: "Montserrat", sans-serif;
  }
  .card {
    position: absolute;
    width: 560px; height: 320px;
    background: var(--paper);
    border-radius: 22px;
    overflow: hidden;
    box-shadow: 0 6px 18px rgba(0,0,0,0.18);
  }
  .card--back { left: 60px; top: 80px; }
  .card--front { left: 580px; top: 452px; }

  .wordmark {
    position: absolute;
    text-align: center;
    color: var(--blue);
    font-weight: 800;
    text-transform: uppercase;
    line-height: 22px;
    letter-spacing: 0.5px;
    white-space: nowrap;
  }
  .wordmark__sub { display: block; letter-spacing: 9px; font-size: 0.8em; }
  .mark-square { position: absolute; background: var(--green); }
  .rule { position: absolute; height: 2px; }
  .rule--blue { background: var(--blue); }
  .rule--green { background: var(--green); }

  /* Back side */
  .card--back .mark-square { left: 250px; top: 28px; width: 60px; height: 60px; }
  .card--back .wordmark { left: 0; right: 0; top: 100px; font-size: 20px; }
  .brands-label {
    position: absolute; left: 0; right: 0; top: 170px;
    text-align: center; font-size: 12px; color: var(--ink); font-weight: 500;
  }
  .brand-row {
    position: absolute; left: 20px; right: 20px; top: 196px;
    display: flex; justify-content: space-between; align-items: center;
  }
  .brand {
    font-size: 16px; font-weight: 700; color: var(--blue);
    display: flex; align-items: center; gap: 6px; white-space: nowrap;
  }
  .brand__dot { width: 14px; height: 14px; border-radius: 50%; background: var(--green); }
  .brand-sep { width: 2px; height: 36px; background: var(--divider); }
  .site-url {
    position: absolute; left: 0; right: 0; top: 264px;
    text-align: center; font-size: 12px; color: var(--ink); font-weight: 500;
  }

  /* Front side */
  .band { position: absolute; inset: 0; }
  .card--front .wordmark { left: 20px; top: 36px; width: 320px; font-size: 19px; }
  .badge {
    position: absolute; left: 418px; top: 38px;
    width: 104px; height: 104px;
    background: var(--green);
    border: 6px solid var(--paper);
  }
  .person { position: absolute; left: 28px; top: 170px; color: var(--paper); }
  .person__name { font-family: "Roboto Condensed", sans-serif; font-size: 21px; font-weight: 700; line-height: 26px; }
  .person__role { font-size: 12px; font-weight: 500; line-height: 16px; margin-bottom: 6px; }
  .contact { list-style: none; margin: 0; padding: 0; font-size: 12.5px; }
  .contact li { display: flex; align-items: center; gap: 10px; line-height: 18px; }
  .contact svg { width: 12px; height: 12px; fill: var(--paper); }
  .address {
    position: absolute; left: 28px; top: 294px;
    font-size: 13px; font-weight: 500; color: var(--ink);
  }
</style>
</head>
<body>

<section class="card card--back" aria-label="Card back">
  <div class="mark-square"></div>
  <div class="rule rule--green" style="left:330px;top:70px;width:200px"></div>
  <div class="wordmark">Harborlight Amusement<span class="wordmark__sub">Collective</span></div>
  <div class="rule rule--blue" style="left:70px;top:132px;width:110px"></div>
  <div class="rule rule--blue" style="left:380px;top:132px;width:110px"></div>
  <div class="rule rule--green" style="left:30px;top:160px;width:500px"></div>
  <p class="brands-label">Our Brands</p>
  <div class="brand-row">
    <span class="brand"><span class="brand__dot"></span>Tidewell Tickets</span>
    <span class="brand-sep"></span>
    <span class="brand">Boxseat Hospitality</span>
    <span class="brand-sep"></span>
    <span class="brand">Gatemark</span>
  </div>
  <div class="rule rule--green" style="left:30px;top:250px;width:500px"></div>
  <p class="site-url">www.harborlightcollective.com</p>
</section>

<section class="card card--front" aria-label="Card front">
  <svg class="band" width="560" height="320" viewBox="0 0 560 320" aria-hidden="true">
    <polygon points="0,160 290,160 380,0 560,0 560,286 0,286" fill="#2457a0"/>
  </svg>
  <div class="wordmark">Harborlight Amusement<span class="wordmark__sub">Collective</span></div>
  <div class="rule rule--blue" style="left:35px;top:68px;width:55px"></div>
  <div class="rule rule--blue" style="left:270px;top:68px;width:55px"></div>
  <div class="badge"></div>
  <div class="person">
    <p class="person__name">Rowan Ellery</p>
    <p class="person__role">Managing Director</p>
    <ul class="contact">
      <li><svg viewBox="0 0 24 24"><path d="M6.6 10.8a15 15 0 006.6 6.6l2.2-2.2a1 1 0 011-.25 11.4 11.4 0 003.6.57 1 1 0 011 1V20a1 1 0 01-1 1A17 17 0 013 4a1 1 0 011-1h3.5a1 1 0 011 1c0 1.25.2 2.45.57 3.57a1 1 0 01-.25 1z"/></svg>555.014.2290</li>
      <li><svg viewBox="0 0 24 24"><path d="M2 5h20v14H2z M3 6l9 7 9-7" fill="none" stroke="#fff" stroke-width="2"/></svg>rowan@harborlightcollective.com</li>
      <li><svg viewBox="0 0 24 24"><circle cx="12" cy="12" r="9" fill="none" stroke="#fff" stroke-width="2"/><path d="M3 12h18M12 3c3 3 3 15 0 18M12 3c-3 3-3 15 0 18" fill="none" stroke="#fff" stroke-width="1.6"/></svg>www.harborlightcollective.com</li>
    </ul>
  </div>
  <p class="address">78 Quayside Ave., Port Merrin, US 102456</p>
</section>

</body>
</html>
```